BildeVOLD buisnesscard

Hey :) I need a modern buisnesscard for my company BildeVOLD
It most have:
Dagligleder og Fotograf: Henrik Audun Strandvik

Mob: +4791264085
Epost: post@bildevold.example
Adresse: Kvernbakken9, 6040 Langevåg

Facbook and instagram logo with text BildeVOLD

BildeVOLD logo

It Company

```html
<!DOCTYPE html>
<html lang="no">
<head>
<meta charset="utf-8">
<title>BildeVOLD – visittkort</title>
<link href="https://fonts.googleapis.com/css2?family=Mulish:ital,wght@0,400;0,600;0,700;1,500&display=swap" rel="stylesheet">
<style>
  :root {
    --backdrop: #ece8e3;
    --card: #4a3f7c;
    --card-deep: #3e3469;
    --card-soft: #5a4f8a;
    --ink-light: #ffffff;
    --ink-mark: #c6c4cc;
    --rule: #342b5c;
  }
  * { box-sizing: border-box; margin: 0; padding: 0; }
  html, body { width: 1200px; height: 902px; overflow: hidden; }
  body {
    background: var(--backdrop);
    font-family: "Mulish", sans-serif;
    position: relative;
  }
  .card {
    position: absolute;
    width: 482px;
    height: 274px;
    background: var(--card);
    box-shadow: 0 10px 24px rgba(0,0,0,0.25);
    overflow: hidden;
  }
  .card--front { left: 116px; top: 326px; }
  .card--back  { left: 656px; top: 322px; }
  .card__photo {
    position: absolute; inset: 0;
    background:
      radial-gradient(circle at 50% 55%, var(--card-deep) 0 22%, transparent 36%),
      radial-gradient(circle at 8% 55%, var(--card-soft) 0 10%, transparent 18%),
      radial-gradient(circle at 92% 50%, var(--card-soft) 0 10%, transparent 18%),
      linear-gradient(180deg, var(--card-soft) 0%, var(--card) 45%, var(--card-deep) 100%);
    opacity: 0.55;
  }
  .brand {
    position: absolute;
    display: flex; align-items: center; gap: 10px;
    color: var(--ink-mark);
    font-weight: 700;
  }
  .brand__square { width: 14px; height: 14px; background: var(--ink-mark); }
  .card--front .brand {
    left: 0; right: 0; top: 108px; justify-content: center;
    font-size: 40px; letter-spacing: 0.5px;
  }
  .card--front .brand__square { width: 22px; height: 22px; }
  .card__rule {
    position: absolute; left: 22px; right: 20px; bottom: 8px;
    height: 2px; background: var(--rule);
  }
  .card--back .brand {
    left: 28px; top: 143px; font-size: 22px;
  }
  .contact {
    position: absolute; right: 27px; top: 106px;
    text-align: right; color: var(--ink-light);
  }
  .contact__name {
    font-style: italic; font-weight: 500;
    font-size: 17.5px; letter-spacing: 1.4px;
  }
  .contact__role {
    margin-top: 11px; font-weight: 700;
    font-size: 11.5px; letter-spacing: 1px;
  }
  .contact__lines { margin-top: 30px; list-style: none; font-size: 12.5px; letter-spacing: 1px; }
  .contact__lines li { line-height: 22.5px; }
</style>
</head>
<body>
  <section class="card card--front">
    <div class="card__photo" role="img" aria-label="Faint photograph of camera lenses and photographers behind the card"></div>
    <div class="brand"><span class="brand__square"></span>BildeVOLD</div>
    <div class="card__rule"></div>
  </section>

  <section class="card card--back">
    <div class="card__photo" role="img" aria-label="Faint photograph of camera lenses and photographers behind the card"></div>
    <div class="brand"><span class="brand__square"></span>BildeVOLD</div>
    <div class="contact">
      <p class="contact__name">Henrik Audun Strandvik</p>
      <p class="contact__role">Dagligleder og Fotograf</p>
      <ul class="contact__lines">
        <li>Mob: +4791264085</li>
        <li>Epost: post@bildevold.example</li>
        <li>Adresse: Kvernbakken9, 6040 Langevåg</li>
      </ul>
    </div>
  </section>
</body>
</html>
```